Business Card Design

This is a new business to be run from my home. I have attended certificate workshops run by Dr Victor Osei who is a Master Trainer in Gentle Moves for Mobility.
I wish to communicate to people that Tai Chi is for everyone, no matter their age, gender or fitness levels. Tai Chi is taught both standing & seated.
The card should have a slightly Asian feel, mainly printed in black & white with perhaps a little soft pink &/or green.

Target Market(s)

people of all ages from 10 years up, poor fitness & mild disabilities.

Industry/Entity Type

Fitness

Contact Information for Business Card

Brookhurst Tai Chi for Fitness, Health & Relaxation

Marnie Holbrook, Certificated Leader

ph 5182 9046

Requirements
Nice to have
• a feeling of health & peace.
Should not have
• bright colours, fancy fonts

```html
<!DOCTYPE html>
<html lang="en">
<head>
<meta charset="utf-8">
<title>Brookhurst Tai Chi for Fitness – Business Card</title>
<link href="https://fonts.googleapis.com/css2?family=Archivo+Black&family=Open+Sans:wght@400;600;700&display=swap" rel="stylesheet">
<style>
  :root {
    --bg: #e4e4e4;
    --card: #ffffff;
    --ink: #111111;
    --band: #1b1d1c;
    --green: #2f9e44;
    --white: #ffffff;
    --art-light: #d9d9d9;
    --art-dark: #6a6a6a;
  }
  html, body {
    margin: 0;
    padding: 0;
    width: 1200px;
    height: 900px;
    overflow: hidden;
    background: var(--bg);
  }
  .canvas {
    position: relative;
    width: 1200px;
    height: 900px;
  }
  .business-card {
    position: absolute;
    left: 100px;
    top: 160px;
    width: 1000px;
    height: 580px;
    background: var(--card);
    border-radius: 44px;
    overflow: hidden;
    box-shadow: 0 10px 30px rgba(0,0,0,0.15);
  }
  .business-name {
    position: absolute;
    left: 60px;
    top: 82px;
    margin: 0;
    font-family: "Archivo Black", "Arial Black", sans-serif;
    font-size: 32px;
    line-height: 1.2;
    color: var(--ink);
    white-space: nowrap;
  }
  .tagline {
    position: absolute;
    left: 320px;
    top: 134px;
    margin: 0;
    font-family: "Open Sans", Arial, sans-serif;
    font-weight: 700;
    font-size: 30px;
    color: var(--green);
    white-space: nowrap;
  }
  .contact-band {
    position: absolute;
    left: 0;
    top: 300px;
    width: 100%;
    height: 180px;
    background: var(--band);
  }
  .band-rule {
    position: absolute;
    left: 0;
    width: 100%;
    height: 6px;
    background: var(--green);
  }
  .band-rule.top { top: 286px; }
  .band-rule.bottom { top: 494px; }
  .leader {
    position: absolute;
    left: 240px;
    top: 322px;
    width: 400px;
    text-align: center;
    font-family: "Open Sans", Arial, sans-serif;
  }
  .leader-name {
    margin: 0;
    font-size: 32px;
    font-weight: 400;
    color: var(--green);
  }
  .leader-title {
    margin: 2px 0 0;
    font-size: 24px;
    font-weight: 400;
    color: var(--white);
  }
  .phone {
    position: absolute;
    left: 240px;
    top: 420px;
    width: 400px;
    display: flex;
    justify-content: center;
    align-items: center;
    gap: 12px;
    font-family: "Open Sans", Arial, sans-serif;
    font-size: 32px;
    color: var(--white);
  }
  .phone-icon { width: 30px; height: 30px; }
  .dragon-art {
    position: absolute;
    left: 790px;
    top: 40px;
    width: 185px;
    height: 510px;
    border-radius: 40px;
    background: linear-gradient(180deg, var(--art-light), var(--art-dark) 55%, var(--art-light));
    opacity: 0.9;
  }
</style>
</head>
<body>
<div class="canvas">
  <div class="business-card">
    <h1 class="business-name">BROOKHURST TAI CHI FOR FITNESS</h1>
    <p class="tagline">Health &amp; Relaxation</p>

    <div class="band-rule top"></div>
    <div class="contact-band"></div>
    <div class="band-rule bottom"></div>

    <div class="leader">
      <p class="leader-name">Marnie Holbrook</p>
      <p class="leader-title">Certificated Leader</p>
    </div>

    <div class="phone">
      <svg class="phone-icon" viewBox="0 0 24 24" aria-hidden="true">
        <path fill="#2f9e44" d="M6.6 10.8c1.4 2.8 3.8 5.1 6.6 6.6l2.2-2.2c.3-.3.7-.4 1-.2 1.1.4 2.3.6 3.6.6.6 0 1 .4 1 1V20c0 .6-.4 1-1 1C10.6 21 3 13.4 3 4c0-.6.4-1 1-1h3.5c.6 0 1 .4 1 1 0 1.3.2 2.5.6 3.6.1.3 0 .7-.2 1z"/>
      </svg>
      <span class="phone-number">5182 9046</span>
    </div>

    <div class="dragon-art" role="img" aria-label="Black and white line illustration of a coiling Chinese dragon holding a yin-yang symbol"></div>
  </div>
</div>
</body>
</html>
```